Fitness & sports performance company needs a landing page design

Looking for a landing page for a fitness & sports performance company based in South Florida. The company is 'The Harbor Motion Studio', and 'The Harbor' for short. The main objective of the landing page is to generate leads, and show potential clients the services we offer, as well as pricing for each service. While we are based in South Florida, we also offer online services such as an online trainer and online strength & conditioning programs. Would like to see designs that utilize the colors in our logo.

Target Market(s)

those looking to lose weight, gain strength and make overall healthy lifestyle changes

Font styles to use
Sans Serif

Colors
60b9df
57b5de

Requirements
Must have
• a place to list testimonials, list of services provided, show pricing for each service, colors of the website matching colors in the logo
Nice to have
• i would like to see a landing page that can be utilized to create leads and an email list

```html
<!DOCTYPE html>
<html lang="en">
<head>
<meta charset="utf-8">
<title>The Harbor Motion Studio</title>
<link href="https://fonts.googleapis.com/css2?family=Exo+2:wght@500;600;700;800&family=Open+Sans:wght@400;600;700&display=swap" rel="stylesheet">
<style>
:root{
  --blue:#57b5de;
  --blue-light:#60b9df;
  --ink:#111111;
  --dark:#141516;
  --dark-2:#1d1f21;
  --grey-text:#444444;
  --muted:#9a9a9a;
  --white:#ffffff;
  --pale:#eef1f6;
  --line:#d8d8d8;
}
*{margin:0;padding:0;box-sizing:border-box}
html,body{width:1200px;height:4100px;overflow:hidden}
body{font-family:"Open Sans",Arial,sans-serif;color:var(--grey-text);background:var(--white);position:relative}
.heading{font-family:"Exo 2",Arial,sans-serif;font-weight:700;text-transform:uppercase;text-align:center;font-size:34px;color:var(--ink);letter-spacing:.5px}
.heading span{color:var(--blue)}
.btn{display:inline-block;background:var(--blue);color:var(--white);font-family:"Exo 2",Arial,sans-serif;font-weight:700;font-size:13px;letter-spacing:1px;text-transform:uppercase;padding:14px 30px;border-radius:3px}
.abs{position:absolute}

/* hero */
.hero{position:absolute;left:0;top:0;width:1200px;height:650px;background:radial-gradient(ellipse 420px 300px at 880px 330px,#7a3a12 0%,#3a1c0c 35%,transparent 70%),linear-gradient(90deg,#050505 0%,#0d0d0d 45%,#2a2625 70%,#141212 100%);overflow:hidden}
.topbar{position:absolute;left:0;top:0;width:1200px;height:38px;background:rgba(0,0,0,.55);display:flex;align-items:center;padding:0 95px;color:var(--white);font-size:13px}
.topbar .item{display:flex;align-items:center;gap:8px}
.topbar .address{margin-left:250px}
.topbar .social{margin-left:auto;display:flex;gap:8px}
.dot{width:18px;height:18px;border-radius:50%;background:var(--white);display:inline-block}
.brand{position:absolute;left:140px;top:60px;display:flex;align-items:center;gap:10px;font-family:"Exo 2",Arial,sans-serif;font-weight:700;font-size:20px;color:var(--white);text-transform:uppercase;width:220px;line-height:1.1}
.brand .mark{width:44px;height:44px;border-radius:50%;background:var(--blue);flex:none}
.hero-title{position:absolute;left:140px;top:280px;font-family:"Exo 2",Arial,sans-serif;font-weight:700;font-size:54px;line-height:1.08;color:var(--white);text-transform:uppercase}
.hero-title span{color:var(--blue)}
.hero-text{position:absolute;left:140px;top:478px;width:420px;color:#dddddd;font-size:14px;line-height:1.5}
.hero-btn{position:absolute;left:140px;top:550px;border:2px solid var(--blue);color:var(--white);font-family:"Exo 2",Arial,sans-serif;font-weight:600;font-size:15px;padding:12px 40px;text-transform:uppercase}
.hero-photo{position:absolute;left:590px;top:0;width:610px;height:650px}
.arrow-btn{position:absolute;top:390px;width:40px;height:40px;border-radius:50%;background:rgba(255,255,255,.35)}
.section-badge{position:absolute;left:572px;width:56px;height:56px;border-radius:50%;background:var(--white);display:flex;align-items:center;justify-content:center;z-index:3}
.section-badge i{width:34px;height:34px;border-radius:50%;background:var(--blue);display:block}

/* about */
.about{position:absolute;left:0;top:650px;width:1200px;height:473px;background:var(--white)}
.about .heading{position:absolute;top:62px;width:100%}
.about-copy{position:absolute;left:95px;top:148px;width:560px}
.about-copy h3{font-size:17px;font-weight:700;color:var(--ink);margin-bottom:18px}
.about-copy p{font-size:13.5px;line-height:1.62;color:#555}
.about-copy .btn{margin-top:26px}
.video{position:absolute;left:698px;top:154px;width:402px;height:264px;background:linear-gradient(135deg,#3a3430,#1a1818 60%,#6d5a4a);border:3px solid #c9c9c9}
.play{position:absolute;left:170px;top:102px;width:60px;height:60px;border-radius:50%;background:rgba(255,255,255,.9)}

/* services */
.services{position:absolute;left:0;top:1123px;width:1200px;height:447px;background:linear-gradient(180deg,#1a1b1d,#111213)}
.services .heading{position:absolute;top:30px;width:100%;color:var(--white)}
.service{position:absolute;width:470px;display:flex;gap:24px}
.service .icon{width:102px;height:102px;flex:none;border:1px solid #3b3d40;position:relative;display:flex;align-items:center;justify-content:center}
.service .icon.filled{background:var(--blue);border:none}
.service .icon .corner{position:absolute;left:0;top:0;width:0;height:0;border-top:22px solid var(--blue);border-right:22px solid transparent}
.service h4{font-family:"Exo 2",Arial,sans-serif;font-weight:700;font-size:18px;color:var(--white);text-transform:uppercase;margin:0 0 8px}
.service h4 span{color:var(--blue)}
.service p{font-size:12px;line-height:1.5;color:#c9c9c9;width:320px}

/* pricing */
.pricing{position:absolute;left:0;top:1570px;width:1200px;height:815px;background:var(--white)}
.pricing .heading{position:absolute;top:62px;width:100%}
.intro{position:absolute;left:200px;width:800px;text-align:center;font-size:13px;line-height:1.6;color:#333}
.card-photo{position:absolute;border:4px solid #d6d6d6}
.price-title{position:absolute;text-align:center;font-family:"Exo 2",Arial,sans-serif;font-weight:700;font-size:18px;color:var(--blue);text-transform:uppercase}
.price-name{position:absolute;text-align:center;font-size:14px;color:#222}
.price{position:absolute;text-align:center;font-size:15px;font-weight:600;color:#222}
.price s{color:#aaa;font-weight:400;margin-right:10px}
.dots{position:absolute;display:flex;gap:6px;justify-content:center}
.dots i{width:10px;height:10px;border-radius:50%;background:#ccc;display:block}
.dots i.on{background:var(--blue)}
.overlay-btn{position:absolute;width:110px;height:32px;border-radius:16px;font-size:12px;font-weight:600;display:flex;align-items:center;justify-content:center}
.nav-arrows{position:absolute;left:561px;top:713px;display:flex;gap:4px}
.nav-arrows span{width:34px;height:34px;display:flex;align-items:center;justify-content:center;border:1px solid #ccc}
.nav-arrows span.dark{background:#111;border-color:#111}

/* online */
.online{position:absolute;left:0;top:2385px;width:1200px;height:835px;background:linear-gradient(135deg,#f3f5f9,#dfe4ec 55%,#eef0f5)}
.online .heading{position:absolute;top:98px;width:100%}
.subhead{position:absolute;display:flex;align-items:center;gap:12px;font-family:"Exo 2",Arial,sans-serif;font-weight:700;font-size:22px;color:var(--ink);text-transform:uppercase}
.subhead span{color:var(--blue)}
.subhead i{width:42px;height:42px;border-radius:50%;background:var(--blue);display:block;border:4px solid #cfe9f5}
.trainer-photo{position:absolute;left:95px;top:320px;width:480px;height:222px;background:linear-gradient(135deg,#e9e4de,#c8c0b6 50%,#8e9da8)}
.date{position:absolute;left:516px;top:472px;width:60px;height:70px;background:var(--blue);color:var(--white);font-family:"Exo 2",Arial,sans-serif;text-align:center;padding-top:10px;line-height:1.1}
.date b{display:block;font-size:22px}
.date small{font-size:14px}
.trainer-title{position:absolute;left:95px;top:570px;font-family:"Exo 2",Arial,sans-serif;font-weight:700;font-size:30px;color:var(--ink)}
.trainer-text{position:absolute;left:95px;top:622px;width:480px;font-size:13.5px;line-height:1.55;color:#333}
.post{position:absolute;left:620px;width:485px;height:132px;background:var(--white);display:flex;box-shadow:0 2px 6px rgba(0,0,0,.08)}
.post .thumb{width:112px;height:132px;flex:none}
.post .body{padding:10px 16px}
.post h5{font-family:"Open Sans",Arial,sans-serif;font-weight:700;font-size:17px;color:var(--ink);margin-bottom:6px}
.post p{font-size:12.5px;line-height:1.4;color:#333}
.post .meta{font-size:10.5px;color:#555;margin-top:8px;display:flex;align-items:center;gap:6px}
.post .meta i{width:12px;height:12px;border-radius:50%;border:1px solid #888;display:block}

/* testimonials */
.testimonials{position:absolute;left:0;top:3220px;width:1200px;height:500px;background:radial-gradient(ellipse 300px 260px at 900px 200px,#6a4030 0%,transparent 70%),linear-gradient(180deg,#4a4f55 0%,#2a2d31 45%,#141516 100%)}
.testimonials .heading{position:absolute;top:100px;width:100%;color:var(--blue)}
.testimonials .intro{color:#e2e2e2;top:163px}
.avatar{position:absolute;left:568px;top:263px;width:64px;height:64px;border-radius:50%;background:#c9ccd0;border:3px solid #e6e6e6}
.client{position:absolute;left:0;top:340px;width:100%;text-align:center;color:var(--white)}
.client b{display:block;font-size:14px;text-transform:uppercase}
.client span{font-size:13px;color:#ccc}

/* footer */
.footer{position:absolute;left:0;top:3720px;width:1200px;height:340px;background:linear-gradient(135deg,#f4f5f7,#e7eaee)}
.footer h6{font-family:"Exo 2",Arial,sans-serif;font-weight:700;font-size:18px;color:var(--blue);text-transform:uppercase;margin-bottom:26px}
.quick{position:absolute;left:95px;top:70px}
.quick li{list-style:none;font-size:13px;font-weight:600;color:#222;text-transform:uppercase;line-height:2.2}
.contact{position:absolute;left:332px;top:70px;width:220px}
.contact .row{display:flex;gap:10px;font-size:13px;color:#222;line-height:1.5;margin-bottom:16px}
.contact .row svg{flex:none;margin-top:3px}
.contact .social{display:flex;gap:8px}
.contact .social i{width:20px;height:20px;border-radius:50%;background:#111;display:block}
.map{position:absolute;left:575px;top:80px;width:250px;height:210px;background:linear-gradient(135deg,#dfe9d8,#c7dbe7 60%,#e7e3d6);border:3px solid var(--blue)}
.map .pin{position:absolute;left:107px;top:70px}
.footer-brand{position:absolute;left:905px;top:120px;display:flex;align-items:center;gap:12px;font-family:"Exo 2",Arial,sans-serif;font-weight:700;font-size:28px;color:var(--ink);text-transform:uppercase;width:260px;line-height:1.1}
.footer-brand .mark{width:60px;height:60px;border-radius:50%;background:var(--blue);flex:none}
.copyright{position:absolute;left:0;top:4060px;width:1200px;height:40px;background:var(--blue);color:var(--white);font-size:13px;font-weight:600;text-transform:uppercase;display:flex;align-items:center;justify-content:center;letter-spacing:.3px}
</style>
</head>
<body>

<header class="hero">
  <div class="hero-photo" role="img" aria-label="Close-up photo of an athlete's running shoe pushing off a track with glowing sparks"></div>
  <div class="topbar">
    <div class="item">
      <svg width="14" height="14" viewBox="0 0 24 24"><path fill="#57b5de" d="M6.6 10.8a15 15 0 006.6 6.6l2.2-2.2c.3-.3.7-.4 1-.2 1.1.4 2.3.6 3.6.6.6 0 1 .4 1 1V20c0 .6-.4 1-1 1A17 17 0 013 4c0-.6.4-1 1-1h3.5c.6 0 1 .4 1 1 0 1.3.2 2.5.6 3.6.1.3 0 .7-.2 1z"/></svg>
      1-800-555-0199
    </div>
    <div class="item address">
      <svg width="12" height="16" viewBox="0 0 12 16"><path fill="#57b5de" d="M6 0a6 6 0 00-6 6c0 4.5 6 10 6 10s6-5.5 6-10a6 6 0 00-6-6zm0 8.5A2.5 2.5 0 116 3.5a2.5 2.5 0 010 5z"/></svg>
      Bayview Point, FL 33000, Lorem Ipsum Dolor
    </div>
    <div class="social"><i class="dot"></i><i class="dot"></i><i class="dot"></i><i class="dot"></i></div>
  </div>
  <div class="brand"><span class="mark"></span>The Harbor Motion Studio</div>
  <h1 class="hero-title"><span>The Harbor</span><br>Motion<br>Studio</h1>
  <p class="hero-text">Lorem Ipsum is simply dummy text of the printing and typesetting industry. Lorem Ipsum has been the industry's standard dummy.</p>
  <div class="hero-btn">Discover</div>
  <div class="arrow-btn" style="left:55px"><svg width="40" height="40" viewBox="0 0 40 40"><path d="M23 13l-7 7 7 7" stroke="#fff" stroke-width="2.5" fill="none"/></svg></div>
  <div class="arrow-btn" style="left:1105px"><svg width="40" height="40" viewBox="0 0 40 40"><path d="M17 13l7 7-7 7" stroke="#fff" stroke-width="2.5" fill="none"/></svg></div>
</header>

<div class="section-badge" style="top:622px"><i></i></div>

<section class="about">
  <h2 class="heading">About <span>The Harbor</span></h2>
  <div class="about-copy">
    <h3>Contrary to popular belief, Lorem Ipsum is not simply random text.</h3>
    <p>Lorem Ipsum is simply dummy text of the printing and typesetting industry. Lorem Ipsum has been the industry's standard dummy text ever since the 1500s, when an unknown printer took a galley of type and scrambled it to make a type specimen book. It has survived not only five centuries, but also the leap into electronic typesetting, remaining essentially unchanged. It was popularised in the 1960s with the release of Letraset sheets containing Lorem Ipsum passages, and more recently with desktop publishing software like Aldus PageMaker including versions of Lorem Ipsum.</p>
    <span class="btn">Read More</span>
  </div>
  <div class="video" role="img" aria-label="Video still of an athlete tying a shoe in a gym">
    <div class="play"><svg width="60" height="60" viewBox="0 0 60 60"><path d="M24 18l18 12-18 12z" fill="#e03a3a"/></svg></div>
  </div>
</section>

<section class="services">
  <h2 class="heading">Our <span>Services</span></h2>
  <div class="service" style="left:115px;top:100px">
    <div class="icon filled"><svg width="44" height="44" viewBox="0 0 44 44"><circle cx="22" cy="12" r="5" fill="#fff"/><path d="M10 36l8-14 10 6 8-10" stroke="#fff" stroke-width="4" fill="none" stroke-linecap="round"/></svg></div>
    <div><h4><span>Fitness</span> Class</h4><p>Lorem Ipsum is simply dummy text of the printing and typesetting industry. Lorem Ipsum has been the industry's standard dummy text ever since the 1500s, when an unknown printer took a galley of type and scrambled it.</p></div>
  </div>
  <div class="service" style="left:630px;top:100px">
    <div class="icon"><span class="corner"></span><svg width="44" height="44" viewBox="0 0 44 44"><rect x="8" y="10" width="12" height="18" rx="5" fill="none" stroke="#fff" stroke-width="2.5"/><rect x="24" y="10" width="12" height="18" rx="5" fill="none" stroke="#fff" stroke-width="2.5"/><rect x="10" y="28" width="8" height="6" fill="#fff"/><rect x="26" y="28" width="8" height="6" fill="#fff"/></svg></div>
    <div><h4><span>Boxing</span> Class</h4><p>Lorem Ipsum is simply dummy text of the printing and typesetting industry. Lorem Ipsum has been the industry's standard dummy text ever since the 1500s, when an unknown printer took a galley of type and scrambled it.</p></div>
  </div>
  <div class="service" style="left:115px;top:282px">
    <div class="icon"><span class="corner"></span><svg width="48" height="44" viewBox="0 0 48 44"><rect x="4" y="14" width="6" height="16" rx="1" fill="#fff"/><rect x="11" y="10" width="6" height="24" rx="1" fill="#fff"/><rect x="17" y="20" width="14" height="4" fill="#fff"/><rect x="31" y="10" width="6" height="24" rx="1" fill="#fff"/><rect x="38" y="14" width="6" height="16" rx="1" fill="#fff"/></svg></div>
    <div><h4><span>Crossfit</span> Class</h4><p>Lorem Ipsum is simply dummy text of the printing and typesetting industry. Lorem Ipsum has been the industry's standard dummy text ever since the 1500s, when an unknown printer took a galley of type and scrambled it.</p></div>
  </div>
  <div class="service" style="left:630px;top:282px">
    <div class="icon"><span class="corner"></span><svg width="44" height="44" viewBox="0 0 44 44"><circle cx="22" cy="25" r="14" fill="none" stroke="#fff" stroke-width="2.5"/><rect x="18" y="5" width="8" height="4" fill="#fff"/><path d="M22 25V16" stroke="#fff" stroke-width="2.5"/></svg></div>
    <div><h4><span>Enduro</span> Class</h4><p>Lorem Ipsum is simply dummy text of the printing and typesetting industry. Lorem Ipsum has been the industry's standard dummy text ever since the 1500s, when an unknown printer took a galley of type and scrambled it.</p></div>
  </div>
</section>

<section class="pricing">
  <h2 class="heading">Pricing <span>For Services</span></h2>
  <p class="intro" style="top:142px">Lorem Ipsum is simply dummy text of the printing and typesetting industry. Lorem Ipsum has been the industry's standard dummy text ever since the 1500s, when an unknown printer took a galley of type and scrambled it to make a type specimen book.</p>

  <div class="card-photo" style="left:45px;top:260px;width:350px;height:180px;background:linear-gradient(135deg,#5b5450,#2c2a2c 55%,#3c4a66)" role="img" aria-label="Photo of a woman doing core exercises on a mat"></div>
  <div class="overlay-btn" style="left:165px;top:320px;background:#fff;color:#222">Details</div>
  <div class="overlay-btn" style="left:165px;top:360px;background:var(--blue);color:#fff">Add to cart</div>
  <svg class="abs" style="left:178px;top:405px" width="84" height="14" viewBox="0 0 84 14"><g fill="#57b5de"><circle cx="7" cy="7" r="4"/><circle cx="24" cy="7" r="4"/><circle cx="41" cy="7" r="4"/><circle cx="58" cy="7" r="4"/><circle cx="75" cy="7" r="4"/></g></svg>
  <div class="price-title" style="left:45px;top:540px;width:350px">Service One</div>
  <div class="price-name" style="left:45px;top:570px;width:350px">This is your product name</div>
  <div class="price" style="left:45px;top:596px;width:350px"><s>$19.00</s>$19.00</div>
  <div class="dots" style="left:45px;top:630px;width:350px"><i></i><i></i><i class="on"></i></div>

  <div class="card-photo" style="left:425px;top:218px;width:350px;height:345px;background:linear-gradient(160deg,#8a8a8a,#3a3a3a 50%,#1a1a1a)" role="img" aria-label="Black and white photo of a person lifting a loaded barbell"></div>
  <div class="price-title" style="left:425px;top:578px;width:350px">Service Two</div>
  <div class="price-name" style="left:425px;top:608px;width:350px">This is your product name</div>
  <div class="price" style="left:425px;top:634px;width:350px"><s>$19.00</s>$19.00</div>
  <div class="dots" style="left:425px;top:668px;width:350px"><i></i><i></i><i class="on"></i></div>

  <div class="card-photo" style="left:805px;top:260px;width:350px;height:180px;background:linear-gradient(135deg,#6b5a4c,#2f2b2a 50%,#8c7f74)" role="img" aria-label="Photo of a trainer guiding a woman on suspension straps"></div>
  <div class="price-title" style="left:805px;top:540px;width:350px">Service Three</div>
  <div class="price-name" style="left:805px;top:570px;width:350px">This is your product name</div>
  <div class="price" style="left:805px;top:596px;width:350px"><s>$19.00</s>$19.00</div>
  <div class="dots" style="left:805px;top:630px;width:350px"><i></i><i></i><i class="on"></i></div>

  <div class="nav-arrows">
    <span class="dark"><svg width="12" height="12" viewBox="0 0 12 12"><path d="M8 2L4 6l4 4" stroke="#fff" stroke-width="2" fill="none"/></svg></span>
    <span><svg width="12" height="12" viewBox="0 0 12 12"><path d="M4 2l4 4-4 4" stroke="#999" stroke-width="2" fill="none"/></svg></span>
  </div>
</section>

<section class="online">
  <h2 class="heading">Online <span>Services</span></h2>
  <p class="intro" style="top:170px;left:170px;width:860px">Lorem Ipsum is simply dummy text of the printing and typesetting industry. Lorem Ipsum has been the industry's standard dummy text ever since the 1500s, when an unknown printer took a galley of type and scrambled it to make a type specimen book.</p>

  <div class="subhead" style="left:95px;top:245px"><i></i>Online <span>Trainer</span></div>
  <div class="trainer-photo" role="img" aria-label="Photo of a laptop showing an online workout session in a bright room"></div>
  <div class="date"><b>01</b><small>Dec</small></div>
  <h3 class="trainer-title">Lorem Ipsum is simply dummy text</h3>
  <p class="trainer-text">Lorem Ipsum is simply dummy text of the printing and typesetting industry. Lorem Ipsum has been the industry's standard dummy text ever since the 1500s, when an unknown printer took a galley of type and scrambled it to make a type specimen book.</p>
  <span class="btn abs" style="left:95px;top:717px;border-radius:22px;text-transform:none;font-size:13px;padding:13px 34px">Read More</span>

  <div class="subhead" style="left:620px;top:245px"><i></i>Online <span>Strength</span></div>
  <div class="post" style="top:320px">
    <div class="thumb" role="img" aria-label="Photo of a rolled blue yoga mat" style="background:linear-gradient(135deg,#7fc6d8,#3d8aa0)"></div>
    <div class="body"><h5>Lorem Ipsum is simply dummy text</h5><p>Lorem Ipsum is simply dummy text of the printing and typesetting industry. Lorem Ipsum has been the industry's standard dummy text ever [+]</p><div class="meta"><i></i>Lorem Ipsum, Century to popular</div></div>
  </div>
  <div class="post" style="top:477px">
    <div class="thumb" role="img" aria-label="Photo of a group fitness class in a studio" style="background:linear-gradient(135deg,#d9b8a0,#9c7a66)"></div>
    <div class="body"><h5>Lorem Ipsum is simply dummy text</h5><p>Lorem Ipsum is simply dummy text of the printing and typesetting industry. Lorem Ipsum has been the industry's standard dummy text ever [+]</p><div class="meta"><i></i>Lorem Ipsum, Century to popular</div></div>
  </div>
  <div class="post" style="top:634px">
    <div class="thumb" role="img" aria-label="Photo of a woman stretching outdoors" style="background:linear-gradient(135deg,#7a8fa8,#3d4656)"></div>
    <div class="body"><h5>Lorem Ipsum is simply dummy text</h5><p>Lorem Ipsum is simply dummy text of the printing and typesetting industry. Lorem Ipsum has been the industry's standard dummy text ever [+]</p><div class="meta"><i></i>Lorem Ipsum, Century to popular</div></div>
  </div>
</section>

<section class="testimonials" role="img" aria-label="Background photo of a runner on an open road at dusk">
  <h2 class="heading">Testimonials</h2>
  <p class="intro">Lorem Ipsum is simply dummy text of the printing and typesetting industry. Lorem Ipsum has been the industry's standard dummy text ever since the 1500s, when an unknown printer took</p>
  <div class="avatar"></div>
  <div class="client"><b>Client Name</b><span>Gym Consultant</span></div>
</section>

<div class="section-badge" style="top:3692px"><i></i></div>

<footer class="footer">
  <div class="quick">
    <h6>Quick Links</h6>
    <ul><li>Home</li><li>About Us</li><li>Our Services</li><li>Price List</li><li>Testimonials</li><li>Contact Us</li></ul>
  </div>
  <div class="contact">
    <h6>Contact Us</h6>
    <div class="row"><svg width="12" height="16" viewBox="0 0 12 16"><path fill="#57b5de" d="M6 0a6 6 0 00-6 6c0 4.5 6 10 6 10s6-5.5 6-10a6 6 0 00-6-6zm0 8.5A2.5 2.5 0 116 3.5a2.5 2.5 0 010 5z"/></svg><span>42 Marina Lane North<br>Lorem Ipsum Dolor</span></div>
    <div class="row"><svg width="14" height="14" viewBox="0 0 24 24"><path fill="#57b5de" d="M6.6 10.8a15 15 0 006.6 6.6l2.2-2.2c.3-.3.7-.4 1-.2 1.1.4 2.3.6 3.6.6.6 0 1 .4 1 1V20c0 .6-.4 1-1 1A17 17 0 013 4c0-.6.4-1 1-1h3.5c.6 0 1 .4 1 1 0 1.3.2 2.5.6 3.6.1.3 0 .7-.2 1z"/></svg><span>1-800-555-0199</span></div>
    <div class="row"><svg width="14" height="12" viewBox="0 0 14 12"><rect x="0.5" y="0.5" width="13" height="11" fill="none" stroke="#57b5de"/><path d="M1 1l6 5 6-5" stroke="#57b5de" fill="none"/></svg><span>info@harbormotion.example</span></div>
    <div class="social"><i></i><i></i><i></i><i></i></div>
  </div>
  <div class="map" role="img" aria-label="Street map showing the studio location">
    <svg class="pin" width="30" height="42" viewBox="0 0 12 16"><path fill="#57b5de" d="M6 0a6 6 0 00-6 6c0 4.5 6 10 6 10s6-5.5 6-10a6 6 0 00-6-6zm0 8.5A2.5 2.5 0 116 3.5a2.5 2.5 0 010 5z"/></svg>
  </div>
  <div class="footer-brand"><span class="mark"></span>The Harbor Motion Studio</div>
</footer>

<div class="copyright">Copyright © 2018 The Harbor Motion Studio. All rights reserved</div>

</body>
</html>
```